Corvane Holdings , new business card design

investment firm with corporate clients . need double sided business card , vertical and horizontal options ,logo must be clear. prefer pantone colors only and sharp design. website also www.corvane.ae

Khalid Bin Tarrafi
Managing Director
Tel. +971 4 387 2940
Mobile +971 50 518 2403
khalid@corvane.ae
Q-Span Plaza, officw 18-B07, Warqa Gardens, Dubai

Contact Information for Business Card

Khalid Bin Tarrafi
Managing Director

Font styles to use
Serif

Colors

Designer to choose colors to be used in the design.

```html
<!DOCTYPE html>
<html lang="en">
<head>
<meta charset="utf-8">
<title>Corvane Holdings – Business Card</title>
<link rel="stylesheet" href="https://fonts.googleapis.com/css2?family=Mulish:wght@700&family=Questrial&display=swap">
<style>
  :root {
    --page: #e6e7ea;
    --card-light: #ffffff;
    --card-light-edge: #f1f2f4;
    --band: #0b0d14;
    --accent: #4d7aa6;
    --icon: #7d9cbc;
    --ink: #14161c;
    --text-light: #ffffff;
  }
  * { box-sizing: border-box; margin: 0; padding: 0; }
  html, body { width: 1200px; height: 900px; overflow: hidden; }
  body {
    background: var(--page);
    font-family: "Questrial", "Century Gothic", sans-serif;
    position: relative;
  }
  .business-card {
    position: absolute;
    left: 150px;
    top: 172px;
    width: 900px;
    height: 555px;
    background: linear-gradient(180deg, var(--card-light) 0%, var(--card-light-edge) 100%);
    box-shadow: 0 18px 40px rgba(0,0,0,0.18);
    overflow: hidden;
  }
  .brand {
    position: absolute;
    left: 0; right: 0;
    top: 130px;
    text-align: center;
    color: var(--ink);
    font-family: "Questrial", "Century Gothic", sans-serif;
    font-size: 44px;
    letter-spacing: 9px;
    text-transform: uppercase;
  }
  .info-band {
    position: absolute;
    left: 0; right: 0;
    top: 300px;
    bottom: 0;
    background: var(--band);
    border-top: 6px solid var(--accent);
  }
  .band-notch {
    position: absolute;
    left: 676px;
    top: 298px;
    width: 36px;
    height: 34px;
  }
  .contact-list {
    position: absolute;
    left: 56px;
    top: 58px;
    list-style: none;
    color: var(--text-light);
    font-size: 25px;
    line-height: 32px;
  }
  .contact-list li { display: flex; align-items: center; gap: 12px; }
  .contact-list svg { width: 20px; height: 20px; flex: none; }
  .person {
    position: absolute;
    right: 55px;
    top: 50px;
    text-align: right;
    color: var(--text-light);
  }
  .person-name {
    font-family: "Mulish", "Century Gothic", sans-serif;
    font-weight: 700;
    font-size: 26px;
    color: var(--accent);
    text-transform: uppercase;
    letter-spacing: 0.5px;
    line-height: 32px;
  }
  .person-title { font-size: 25px; line-height: 32px; }
  .address { margin-top: 16px; font-size: 25px; line-height: 32px; font-style: normal; }
</style>
</head>
<body>
  <div class="business-card">
    <div class="brand">Corvane Holdings</div>

    <div class="info-band">
      <ul class="contact-list">
        <li>
          <svg viewBox="0 0 20 20" aria-hidden="true"><path fill="var(--icon)" d="M2 7c0-3 3-4 8-4s8 1 8 4v2h-4V7H6v2H2z M5 10h10l2 7H3z"/><circle cx="10" cy="13.5" r="2" fill="var(--band)"/></svg>
          +971 4 387 2940
        </li>
        <li>
          <svg viewBox="0 0 20 20" aria-hidden="true"><rect x="5" y="1" width="10" height="18" rx="2" fill="var(--icon)"/><rect x="7" y="3.5" width="6" height="11" fill="var(--band)"/><circle cx="10" cy="16.8" r="1" fill="var(--band)"/></svg>
          +971 50 518 2403
        </li>
        <li>
          <svg viewBox="0 0 20 20" aria-hidden="true"><rect x="1" y="4" width="18" height="12" fill="var(--icon)"/><path d="M1.5 4.5 10 11l8.5-6.5" fill="none" stroke="var(--band)" stroke-width="1.5"/></svg>
          khalid@corvane.ae
        </li>
        <li>
          <svg viewBox="0 0 20 20" aria-hidden="true"><circle cx="10" cy="10" r="8.5" fill="var(--icon)"/><path d="M6 5c2 1 3 3 2 5s1 3 3 3l-1 4M13 4c-1 2 0 3 2 3l2 1" fill="none" stroke="var(--band)" stroke-width="1.6"/></svg>
          www.corvane.ae
        </li>
      </ul>

      <div class="person">
        <p class="person-name">Khalid Bin Tarrafi</p>
        <p class="person-title">Managing Director</p>
        <address class="address">Q-Span Plaza, officw 18-B07<br>Warqa Gardens, Dubai</address>
      </div>
    </div>

    <svg class="band-notch" viewBox="0 0 36 34" aria-hidden="true">
      <path d="M0 2 H36 L18 32 Z" fill="var(--card-light-edge)"/>
      <path d="M0 4 L18 32 L36 4" fill="none" stroke="var(--accent)" stroke-width="3"/>
      <rect x="0" y="0" width="36" height="2" fill="var(--card-light-edge)"/>
    </svg>
  </div>
</body>
</html>
```